Local Roofing/Construction company business needs new biz card design

We need a new business card design, current cards are from the start of this operation and generic at best. We are a local Construction Company (General Contractor) with a majority of our work originating from insurance claims-exterior finish work is the main focus (Roofs-Siding-Gutters etc). Heavily involved with homeowners and the low ball offers they receive from insurance company's after a insurable event takes place. I have attached some of our original logo file(s) below.

```html
<!DOCTYPE html>
<html lang="en">
<head>
<meta charset="utf-8">
<title>Stonecrest Builders – Business Card</title>
<link rel="stylesheet" href="https://fonts.googleapis.com/css2?family=Poppins:wght@300;400;600;700&display=swap">
<style>
  :root {
    --green: #2fd67a;
    --green-deep: #1fa85c;
    --green-light: #3bf08f;
    --ink: #1d1d1d;
    --muted: #555555;
    --rule: #9a9a9a;
    --paper: #ffffff;
    --backdrop: #2a2a2a;
  }
  * { box-sizing: border-box; margin: 0; padding: 0; }
  html, body {
    width: 1200px; height: 1108px; overflow: hidden;
    background: var(--backdrop);
    font-family: "Poppins", sans-serif;
  }
  .stage {
    position: relative; width: 1200px; height: 1108px;
    display: flex; justify-content: center; align-items: center; gap: 90px;
  }
  .card {
    width: 400px; height: 680px; border-radius: 26px; overflow: hidden;
    position: relative;
  }
  .card-front {
    background: var(--paper);
    display: flex; flex-direction: column; align-items: center;
    padding: 70px 40px 0;
  }
  .brand {
    display: flex; flex-direction: column; align-items: center; gap: 14px;
    margin-bottom: 56px;
  }
  .brand-square { width: 120px; height: 120px; background: var(--green); border-radius: 14px; }
  .brand-name {
    color: var(--green); font-weight: 700; font-size: 30px; letter-spacing: 2px;
    text-transform: uppercase; text-align: center; line-height: 1.15;
  }
  .person-name {
    color: var(--green); font-weight: 700; font-size: 30px; letter-spacing: 1px;
    text-transform: uppercase;
  }
  .person-title {
    color: var(--ink); font-weight: 400; font-size: 15px; letter-spacing: 1px;
    text-transform: uppercase; margin-top: 2px;
  }
  .icon-row {
    display: flex; align-items: center; gap: 8px; width: 290px; margin: 22px 0 16px;
  }
  .icon-row .rule { flex: 1; height: 1px; background: var(--rule); }
  .icon-box {
    width: 30px; height: 30px; background: var(--green); border-radius: 6px;
    display: flex; align-items: center; justify-content: center;
  }
  .icon-box svg { width: 18px; height: 18px; }
  .contact-list { list-style: none; text-align: center; color: var(--ink); font-size: 17px; line-height: 1.5; }
  .divider { width: 290px; height: 1px; background: var(--rule); margin: 16px 0 14px; }
  .address { font-style: normal; text-align: center; color: var(--ink); font-size: 17px; line-height: 1.5; }
  .card-back { background: var(--green); }
  .back-pattern {
    position: absolute; inset: 0;
    background: linear-gradient(160deg, var(--green-light) 0%, var(--green) 45%, var(--green-deep) 100%);
  }
  .back-name {
    position: absolute; right: 56px; bottom: 150px;
    color: var(--paper); font-weight: 700; font-size: 22px; letter-spacing: 2px;
    text-transform: uppercase;
  }
</style>
</head>
<body>
<main class="stage">
  <section class="card card-front">
    <div class="brand">
      <div class="brand-square"></div>
      <div class="brand-name">Stonecrest<br>Builders</div>
    </div>
    <h1 class="person-name">Daniel Harper</h1>
    <p class="person-title">Managing Director</p>
    <div class="icon-row">
      <span class="rule"></span>
      <span class="icon-box"><svg viewBox="0 0 24 24" fill="#fff"><path d="M6.6 10.8a15 15 0 0 0 6.6 6.6l2.2-2.2a1 1 0 0 1 1-.25 11.4 11.4 0 0 0 3.6.57 1 1 0 0 1 1 1V20a1 1 0 0 1-1 1A17 17 0 0 1 3 4a1 1 0 0 1 1-1h3.5a1 1 0 0 1 1 1c0 1.25.2 2.45.57 3.57a1 1 0 0 1-.25 1z"/></svg></span>
      <span class="icon-box"><svg viewBox="0 0 24 24" fill="none" stroke="#fff" stroke-width="2"><rect x="3" y="5" width="18" height="14" rx="1"/><path d="M3 6l9 7 9-7"/></svg></span>
      <span class="icon-box"><svg viewBox="0 0 24 24" fill="none" stroke="#fff" stroke-width="2"><circle cx="12" cy="12" r="9"/><path d="M3 12h18M12 3c3 3 3 15 0 18M12 3c-3 3-3 15 0 18"/></svg></span>
      <span class="rule"></span>
    </div>
    <ul class="contact-list">
      <li>044-555 018 240</li>
      <li>hello@stonecrestbuild.com</li>
      <li>www.stonecrestbuild.com</li>
    </ul>
    <div class="divider"></div>
    <address class="address">421, Address line goes here<br>45452, Country Name</address>
  </section>
  <section class="card card-back">
    <div class="back-pattern" role="img" aria-label="Repeating embossed brand monogram pattern in shades of green"></div>
    <div class="back-name">Stonecrest</div>
  </section>
</main>
</body>
</html>
```